LotusNINE yoga mats

Design of the yoga mat boxing. You will find sizing and empty box template in the attached files. We also attached some examples of what style we like from various yoga companies. The design should be minimalistic black / white. Can have geometrics, polygons, mandalas or whatever on it. There should also be a placeholder barcode and some space for the companies name, address and contact.

Our company name:
LotusNINE
Brenntalweg 34
AT- 1260 Vienna

www.lotusnine-demo.eu

```html
<!DOCTYPE html>
<html lang="en">
<head>
<meta charset="utf-8">
<title>LotusNINE – Yoga Mat Box</title>
<link href="https://fonts.googleapis.com/css2?family=Lato:wght@400&display=swap" rel="stylesheet">
<style>
  :root {
    --backdrop: #efeee9;
    --panel: #ffffff;
    --ink: #1d1d1b;
    --ring-grey: #a7a8ab;
    --dark-grey: #6d6e71;
    --soft-grey: #cfd0d2;
    --dot-tint: #e4e4e6;
  }
  html, body {
    margin: 0;
    width: 1200px;
    height: 639px;
    overflow: hidden;
    background: var(--backdrop);
    font-family: "Lato", sans-serif;
  }
  .box-face {
    position: absolute;
    left: 50px;
    top: 110px;
    width: 1100px;
    height: 420px;
    background: var(--panel);
    overflow: hidden;
    box-shadow: 0 2px 8px rgba(0,0,0,0.08);
  }
  .box-face__art {
    position: absolute;
    inset: 0;
  }
  .brand {
    position: absolute;
    left: 48px;
    top: 40px;
    display: flex;
    align-items: center;
    gap: 14px;
    color: var(--ink);
    font-size: 30px;
    letter-spacing: 0.06em;
  }
  .brand__square {
    width: 26px;
    height: 26px;
    border: 2px solid var(--ink);
    box-sizing: border-box;
  }
  .contact {
    position: absolute;
    left: 70px;
    top: 262px;
    color: var(--ink);
    font-size: 18px;
    line-height: 1.35;
  }
  .contact p { margin: 0; }
  .contact__web { margin-top: 22px !important; }
</style>
</head>
<body>
  <main class="box-face">
    <svg class="box-face__art" width="1100" height="420" viewBox="0 0 1100 420">
      <circle class="ring" cx="420" cy="330" r="165" fill="none" stroke="var(--ring-grey)" stroke-width="62"/>
      <rect class="top-bar" x="540" y="0" width="190" height="22" fill="var(--dark-grey)"/>
      <rect class="dot-field" x="620" y="32" width="150" height="90" fill="var(--dot-tint)" role="img" aria-label="Grid of small black dots"/>
      <polygon class="arrow-shape" points="830,130 1100,50 1100,120 1020,180 960,150 890,225" fill="var(--dark-grey)"/>
      <circle class="hatched-disc" cx="950" cy="340" r="68" fill="var(--soft-grey)" role="img" aria-label="Circle filled with fine diagonal line hatching"/>
    </svg>

    <div class="brand">
      <span class="brand__square"></span>
      <span class="brand__name">LotusNINE</span>
    </div>

    <address class="contact" style="font-style:normal">
      <p>Brenntalweg 34</p>
      <p>AT- 1260 Vienna</p>
      <p class="contact__web">www.lotusnine-demo.eu</p>
    </address>
  </main>
</body>
</html>
```